Maple Roster Business Card for recruitment company

We are looking for a Business Card Design that incorporates our personal details and our busines name and logo. We are a specialized search consultancy that recruit Property and Construction professionals.
We would like a business card that stands out and is appealing to the Construction and Property industry as well.

Target Market(s)

people in the construction and property industry

Contact Information for Business Card

Business Name and logo

Font styles to use
Serif

Colors
0094D4
00A9DD
6FCCEA
C7EBF8
E9F6FB

Requirements
Must have
• Business name and logo as well as contact details
Should not have
• No photos of us please

```html
<!DOCTYPE html>
<html lang="en">
<head>
<meta charset="utf-8">
<title>Maple Roster — Business Card</title>
<link rel="stylesheet" href="https://fonts.googleapis.com/css2?family=Lora:wght@400;500;600;700&display=swap">
<style>
  :root {
    --stage: #2e2f31;
    --card-dark: #0e4256;
    --card-light: #ffffff;
    --ink: #0e4256;
    --ink-soft: #1d1d1d;
    --on-dark: #ffffff;
    --blue-strong: #0094d4;
    --blue-mid: #00a9dd;
    --blue-light: #6fccea;
    --blue-pale: #c7ebf8;
    --blue-mist: #e9f6fb;
  }
  * { box-sizing: border-box; margin: 0; padding: 0; }
  html, body {
    width: 1200px; height: 900px; overflow: hidden;
    background: var(--stage);
    font-family: "Lora", Georgia, serif;
  }
  .stage {
    width: 1200px; height: 900px;
    display: flex; flex-direction: column; align-items: center; justify-content: center;
    gap: 36px;
  }
  .card {
    position: relative;
    width: 700px; height: 400px;
    border-radius: 18px;
    overflow: hidden;
  }
  .card--front {
    background: var(--card-dark);
    display: flex; align-items: center; justify-content: center;
    border-bottom: 10px solid var(--blue-strong);
  }
  .brand {
    display: flex; align-items: center; gap: 18px;
  }
  .brand__mark {
    flex: none; border-radius: 50%;
  }
  .wordmark {
    font-weight: 400;
    letter-spacing: 0.06em;
    text-transform: uppercase;
    white-space: nowrap;
    line-height: 1;
  }
  .card--front .brand__mark { width: 44px; height: 44px; background: var(--blue-light); }
  .card--front .wordmark { color: var(--on-dark); font-size: 52px; }

  .card--back {
    background: linear-gradient(180deg, var(--card-light) 0%, var(--card-light) 70%, var(--blue-mist) 100%);
  }
  .card--back .brand {
    position: absolute; top: 54px; right: 46px; gap: 12px;
  }
  .card--back .brand__mark { width: 26px; height: 26px; background: var(--blue-mid); }
  .card--back .wordmark { color: var(--ink); font-size: 32px; }

  .holder {
    position: absolute; top: 128px; left: 0;
    display: flex; align-items: flex-start; gap: 22px;
  }
  .holder__marker {
    width: 24px; height: 44px; background: var(--blue-strong);
  }
  .holder__name {
    color: var(--ink); font-weight: 700; font-size: 24px;
    letter-spacing: 0.04em; text-transform: uppercase; line-height: 1.15;
  }
  .holder__role {
    color: var(--ink-soft); font-size: 16px; font-weight: 400;
  }
  .contact {
    position: absolute; left: 372px; top: 226px;
    color: var(--ink-soft); font-size: 15.5px; line-height: 1.4;
    list-style: none;
  }
  .contact__address { margin-bottom: 12px; }
  .contact__item { display: flex; align-items: center; gap: 10px; }
  .contact__icon { width: 14px; height: 14px; flex: none; }
  .accent-band {
    position: absolute; left: 0; bottom: 0; width: 100%; height: 10px;
    background: linear-gradient(90deg, var(--blue-strong), var(--blue-mid) 50%, var(--blue-light));
  }
</style>
</head>
<body>
<main class="stage">
  <section class="card card--front" aria-label="Card front">
    <div class="brand">
      <span class="brand__mark"></span>
      <h1 class="wordmark">Maple Roster</h1>
    </div>
  </section>

  <section class="card card--back" aria-label="Card back">
    <div class="brand">
      <span class="brand__mark"></span>
      <p class="wordmark">Maple Roster</p>
    </div>

    <div class="holder">
      <span class="holder__marker"></span>
      <div>
        <p class="holder__name">Owen Carlisle</p>
        <p class="holder__role">Director</p>
      </div>
    </div>

    <ul class="contact">
      <li class="contact__address">1187 Birchwood Lane Salem,<br>OR 97301</li>
      <li class="contact__item">
        <svg class="contact__icon" viewBox="0 0 16 16" aria-hidden="true"><path d="M4 1.5l2.5 3-1.5 1.8c.8 1.8 2 3 3.8 3.8l1.8-1.5 3 2.5-1.6 2.4C7.5 13 3 8.5 1.5 3.1z" fill="var(--blue-strong)"/></svg>
        (555) 218-4430
      </li>
      <li class="contact__item">
        <svg class="contact__icon" viewBox="0 0 16 16" aria-hidden="true"><rect x="1.5" y="3.5" width="13" height="9" fill="none" stroke="var(--blue-strong)" stroke-width="1.4"/><path d="M1.5 3.5L8 9l6.5-5.5" fill="none" stroke="var(--blue-strong)" stroke-width="1.4"/></svg>
        hello@mapleroster.com
      </li>
      <li class="contact__item">
        <svg class="contact__icon" viewBox="0 0 16 16" aria-hidden="true"><circle cx="8" cy="8" r="6.5" fill="none" stroke="var(--blue-strong)" stroke-width="1.3"/><ellipse cx="8" cy="8" rx="2.8" ry="6.5" fill="none" stroke="var(--blue-strong)" stroke-width="1.1"/><path d="M1.5 8h13M2.5 5h11M2.5 11h11" stroke="var(--blue-strong)" stroke-width="1"/></svg>
        www.mapleroster.com
      </li>
    </ul>

    <span class="accent-band"></span>
  </section>
</main>
</body>
</html>
```